Fine Art business needs new website

We need a simple website with a home page, about us page, New sculptures, Sold sculptures, and a contact us page.Our sculptures are very high end one of a kind pieces. As such we need the site to be VERY elegant and professional. Lastly, because I'll be updating pictures on the website on a monthly basis it needs to be user friendly to update (Wordpress is preferred). The only branding we have so far for the business is a business card.
Updates
I wasn't completely ready when this project launched, also I am on the road right now and haven't been able to be as responsive to all you designers as I would like. I will work on giving feedback to all the top designs we've received so far. Thank you all so much for your participation and hardwork.
Target Market(s)
High end customers (affluent), art collectors, interior decorators/designers
Industry/Entity Type
Art Gallery
Coding
Coded - Design and coding required
Number of Pages Required
5+ page
Requirements
Must have
- Easily editable picture gallery for myself so that I can add new pieces(pictures of the pieces), remove sold pieces, etc. I would like the website to be built in wordpress so I can update it. I currently use mangewordpress through Netmarro for my other business website and would like to do the same for this one.
- Pages:
- -Intro page with featured pieces
- -Current pieces gallery (for sale) mainly a picture gallery
- -Sculptures archive (sold pieces) another picture gallery
- -About us: Pull-down of -about the artist (attached content)
- -Artistic Process (attached content)
- -Show Schedule:
- -one page dedicated to "friends of TMV" (basically a link page)
- TO BE CLEAR "www.pineroverslane.com" IS A TOTALLY DIFFERENT SITE AND I'M NOT TRYING TO COMBINE THE TWO OR JOIN THEM INTO ONE. This page needs be more elegant and seperate from The Pine Rovers site.
- UPDATE: I'd like a link to the TMV Facebook page: https://www.faceplume-social.com/mirelcraftworks/
Nice to have
- I would like the pictures on the gallery pages able to have text connected with them (Materials, price)
- I would like the site style and fonts to be similar to our business cards we've already had designed (picture attached).
Should not have
- Too much flash or other things that will make the site slow to load.

```html
<!DOCTYPE html>
<html lang="en">
<head>
<meta charset="utf-8">
<title>Contact Us – Tidemere Vale Studios</title>
<link rel="stylesheet" href="https://fonts.googleapis.com/css2?family=Cinzel:wght@400;700&family=Poppins:wght@300;400;500&display=swap">
<style>
:root{
  --purple:#5b0f8e;
  --purple-dark:#3b1a4f;
  --ink:#1d1d1d;
  --text:#333;
  --muted:#666;
  --line:#cfcfcf;
  --white:#fff;
  --map:#f2f2f2;
  --hero-a:#2a0f45;
  --hero-b:#6b3c9c;
}
*{margin:0;padding:0;box-sizing:border-box}
html,body{width:1200px;height:2413px;overflow:hidden;background:var(--white)}
body{position:relative;font-family:'Poppins',sans-serif;color:var(--text)}
.abs{position:absolute}
.center-x{left:0;width:1200px;text-align:center}

/* header */
.contact-line{left:100px;display:flex;align-items:center;gap:12px;font-size:14px;color:var(--muted);font-weight:300}
.icon-ring{width:26px;height:26px;border-radius:50%;border:1px solid #999;display:flex;align-items:center;justify-content:center}
.brand{top:52px;font-family:'Cinzel',serif;font-size:28px;letter-spacing:4px;color:var(--ink)}
.social{display:flex;gap:16px}
.social-dot{width:38px;height:38px;border-radius:50%;display:flex;align-items:center;justify-content:center}
.dot-a{background:#4a1e8a}.dot-b{background:#7a1e4e}.dot-c{background:#b8281c}.dot-d{background:#1f5a9c}
.nav{top:187px;height:49px;border-top:1px solid var(--line);display:flex;align-items:center;font-family:'Cinzel',serif;font-size:14px;color:var(--ink)}
.nav span{position:absolute;transform:translateX(-50%)}

/* hero */
.hero{top:236px;left:0;width:1200px;height:332px;background:radial-gradient(ellipse at 60% 40%,var(--hero-b),var(--hero-a) 75%)}
.hero-title{top:360px;font-family:'Cinzel',serif;font-weight:700;font-size:70px;color:var(--white);letter-spacing:1px}

/* contact */
.section-title{top:655px;font-family:'Cinzel',serif;font-size:48px;color:var(--ink)}
.section-sub{top:745px;font-size:23px;color:var(--ink)}
.info{left:145px;width:240px;text-align:center;font-size:15px;color:var(--ink)}
.info-ring{left:241px;width:48px;height:48px;border-radius:50%;border:1.5px solid var(--purple);display:flex;align-items:center;justify-content:center}
.field{left:491px;width:610px;height:50px;border:1px solid var(--line);font-size:15px;color:var(--muted);padding:14px 17px}
.verify{left:492px;top:1180px;width:318px;height:85px;border:1px solid #d6d6d6;background:#f9f9f9;box-shadow:0 0 3px rgba(0,0,0,.15);font-size:15px;color:var(--ink)}
.send{left:992px;top:1224px;width:107px;height:42px;background:var(--purple);color:var(--white);font-weight:500;font-size:14px;display:flex;align-items:center;justify-content:center;letter-spacing:.5px}

/* map */
.map{top:1369px;left:0;width:1200px;height:471px;background:linear-gradient(135deg,#eeeeee,#f6f6f6 50%,#ebebeb)}
.map-card{left:489px;top:1667px;width:206px;height:86px;background:var(--white);box-shadow:0 1px 4px rgba(0,0,0,.25);text-align:center;font-size:11px;color:var(--ink);padding-top:10px;line-height:24px}
.map-card b{font-weight:400;color:var(--purple);font-size:14px}

/* footer */
.footer-brand{top:1960px;font-family:'Cinzel',serif;font-size:20px;letter-spacing:3px;color:var(--ink)}
.footer-title{top:2055px;font-family:'Cinzel',serif;font-size:30px;color:var(--ink)}
.footer-copy{top:2106px;font-size:15px;line-height:27px;color:var(--ink)}
.subscribe{left:371px;top:2188px;width:458px;height:45px;display:flex}
.subscribe .input{flex:1;border:1px solid #999;border-right:none;padding:12px 14px;font-size:15px;color:var(--muted)}
.subscribe .btn{width:129px;background:var(--purple-dark);color:var(--white);display:flex;align-items:center;justify-content:center;font-size:15px;letter-spacing:1.5px}
.footer-social{top:2259px;left:503px}
.copyright{top:2380px;font-size:12px;color:var(--muted)}
</style>
</head>
<body>

<header>
  <div class="abs contact-line" style="top:11px">
    <span class="icon-ring"><svg width="12" height="12" viewBox="0 0 24 24"><path fill="#555" d="M6.6 10.8a15 15 0 0 0 6.6 6.6l2.2-2.2c.3-.3.7-.4 1-.2 1.1.4 2.3.6 3.6.6.6 0 1 .4 1 1V20c0 .6-.4 1-1 1A17 17 0 0 1 3 4c0-.6.4-1 1-1h3.5c.6 0 1 .4 1 1 0 1.3.2 2.5.6 3.6.1.3 0 .7-.2 1z"/></svg></span>
    (555) 014-2290
  </div>
  <div class="abs contact-line" style="top:48px">
    <span class="icon-ring"><svg width="12" height="10" viewBox="0 0 24 18"><path fill="#555" d="M0 0h24v2L12 10 0 2zM0 5l12 8 12-8v13H0z"/></svg></span>
    mara@pineroverslane.com
  </div>
  <div class="abs center-x brand">TIDEMERE VALE STUDIOS</div>
  <div class="abs social" style="left:902px;top:4px">
    <span class="social-dot dot-a" role="img" aria-label="Faceplume"></span>
    <span class="social-dot dot-b" role="img" aria-label="Photo network"></span>
    <span class="social-dot dot-c" role="img" aria-label="Social network"></span>
    <span class="social-dot dot-d"><svg width="16" height="12" viewBox="0 0 24 18"><path fill="#fff" d="M0 0h24v2L12 10 0 2zM0 5l12 8 12-8v13H0z"/></svg></span>
  </div>
  <nav class="abs nav" style="left:0;width:1200px">
    <span style="left:234px">HOME</span>
    <span style="left:354px">ABOUT US</span>
    <span style="left:511px">NEW SCULPTURES</span>
    <span style="left:694px">SOLD SCULPTURES</span>
    <span style="left:862px">CONTACT US</span>
    <span style="left:977px"><svg width="13" height="13" viewBox="0 0 24 24"><circle cx="10" cy="10" r="7" fill="none" stroke="#1d1d1d" stroke-width="3"/><path d="M15 15l7 7" stroke="#1d1d1d" stroke-width="3"/></svg></span>
  </nav>
</header>

<section>
  <div class="abs hero" role="img" aria-label="Close-up photograph of amethyst crystals"></div>
  <h1 class="abs center-x hero-title">CONTACT US</h1>
</section>

<main>
  <h2 class="abs center-x section-title">Contact Us</h2>
  <p class="abs center-x section-sub">Get in touch with us</p>

  <div class="abs info" style="top:820px;font-size:18px">Address</div>
  <div class="abs info-ring" style="top:868px"><svg width="14" height="18" viewBox="0 0 24 32"><path fill="#5b0f8e" d="M12 0a12 12 0 0 0-12 12c0 9 12 20 12 20s12-11 12-20A12 12 0 0 0 12 0zm0 17a5 5 0 1 1 0-10 5 5 0 0 1 0 10z"/></svg></div>
  <div class="abs info" style="top:928px;line-height:30px">The Pine Rovers,PO box<br>408213 Alderwick CO 80999</div>
  <div class="abs info-ring" style="top:1014px"><svg width="16" height="12" viewBox="0 0 24 18"><path fill="#5b0f8e" d="M0 0h24v2L12 10 0 2zM0 5l12 8 12-8v13H0z"/></svg></div>
  <div class="abs info" style="top:1075px">mara@pineroverslane.com</div>
  <div class="abs info-ring" style="top:1125px"><svg width="15" height="15" viewBox="0 0 24 24"><path fill="#5b0f8e" d="M6.6 10.8a15 15 0 0 0 6.6 6.6l2.2-2.2c.3-.3.7-.4 1-.2 1.1.4 2.3.6 3.6.6.6 0 1 .4 1 1V20c0 .6-.4 1-1 1A17 17 0 0 1 3 4c0-.6.4-1 1-1h3.5c.6 0 1 .4 1 1 0 1.3.2 2.5.6 3.6.1.3 0 .7-.2 1z"/></svg></div>
  <div class="abs info" style="top:1185px">+1.5550142290</div>

  <div class="abs field" style="top:830px">Name</div>
  <div class="abs field" style="top:897px">Email</div>
  <div class="abs field" style="top:963px">Subject</div>
  <div class="abs field" style="top:1030px;height:132px">Message</div>
  <div class="abs verify">
    <svg class="abs" style="left:12px;top:26px" width="34" height="34"><circle cx="17" cy="17" r="13" fill="none" stroke="#4a90e2" stroke-width="3"/></svg>
    <span class="abs" style="left:56px;top:32px">I'm not a robot</span>
    <span class="abs" style="left:245px;top:58px;font-size:9px;color:#777">Privacy · Terms</span>
  </div>
  <div class="abs send">SEND</div>
</main>

<section>
  <div class="abs map" role="img" aria-label="Street map showing the studio location"></div>
  <svg class="abs" style="left:571px;top:1612px" width="24" height="36" viewBox="0 0 24 36"><path fill="#e53935" d="M12 0a12 12 0 0 0-12 12c0 9 12 24 12 24s12-15 12-24A12 12 0 0 0 12 0z"/><circle cx="12" cy="12" r="4" fill="#8b1a1a"/></svg>
  <div class="abs map-card">The Pine Rovers,PO box<br>408213 Alderwick CO 80999<br><b>Tidemere Vale Studio</b></div>
</section>

<footer>
  <div class="abs center-x footer-brand">TIDEMERE VALE STUDIOS</div>
  <h3 class="abs center-x footer-title" style="font-weight:400">Get In Touch With Us</h3>
  <p class="abs center-x footer-copy">At vero eos et accusamus et iusto odio dignissimos ducimus qui<br>blanditiis praesentium voluptatum deleniti atque</p>
  <div class="abs subscribe"><div class="input">Enter Your Email Addresss</div><div class="btn">SUBSCRIBE</div></div>
  <div class="abs social footer-social">
    <span class="social-dot dot-a" role="img" aria-label="Faceplume"></span>
    <span class="social-dot dot-b" role="img" aria-label="Photo network"></span>
    <span class="social-dot dot-c" role="img" aria-label="Social network"></span>
    <span class="social-dot dot-d"><svg width="16" height="12" viewBox="0 0 24 18"><path fill="#fff" d="M0 0h24v2L12 10 0 2zM0 5l12 8 12-8v13H0z"/></svg></span>
  </div>
  <p class="abs center-x copyright">© Copyrights 2018 Tidemere Vale Studio.All Rights Reserved</p>
</footer>

</body>
</html>
```